Business cards and stationary design

We just completed the design of our new logo and we need to print new business cards and letterhead for our nonprofit. We are looking for a fresh new design that shows off our new logo. On letterhead, we must have a column on the right or left to include our Board of Directors (up to 45 names) (see attachment)

Industry/Entity Type

Non-Profit

Contact Information for Business Card

Standard business card with name, title, Company name, mailing address phone numbers, email address and website. Tagline on back "Opening doors for every family"

Font styles to use
Sans Serif

Requirements
Must have
• include pertinent information above
• new logo
• fonts compatible with logo
• should use logo colors only
Nice to have
• tag lines

```html
<!DOCTYPE html>
<html lang="en">
<head>
<meta charset="utf-8">
<title>Shelter Bridge Alliance – Business Card</title>
<link rel="stylesheet" href="https://fonts.googleapis.com/css2?family=Michroma&family=Arimo:wght@400&display=swap">
<style>
  :root {
    --backdrop: #e6e6e6;
    --card: #f8f8f8;
    --teal: #1b7f9e;
    --red: #e1262c;
    --yellow: #f5b324;
    --ink: #555555;
    --faint: #e4edf2;
  }
  html, body {
    margin: 0;
    width: 1200px;
    height: 582px;
    overflow: hidden;
    background: var(--backdrop);
  }
  .canvas {
    position: relative;
    width: 1200px;
    height: 582px;
  }
  .card {
    position: absolute;
    top: 158px;
    width: 464px;
    height: 264px;
    background: var(--card);
    overflow: hidden;
    box-shadow: 1px 2px 4px rgba(0,0,0,0.35);
  }
  .card--front { left: 122px; }
  .card--back  { left: 602px; }

  .holder {
    position: absolute;
    left: 48px;
    top: 64px;
  }
  .holder__name {
    margin: 0;
    font-family: "Michroma", sans-serif;
    font-size: 14.5px;
    font-weight: 400;
    letter-spacing: 1.2px;
    color: var(--teal);
    line-height: 18px;
  }
  .holder__title {
    margin: 0 0 12px;
    font-family: "Michroma", sans-serif;
    font-size: 9px;
    letter-spacing: 1.4px;
    color: var(--red);
    line-height: 12px;
  }
  .address, .contacts {
    margin: 0;
    font-family: "Arimo", sans-serif;
    font-size: 11px;
    line-height: 13.7px;
    color: var(--ink);
    font-style: normal;
  }
  .contacts {
    list-style: none;
    padding: 0;
    margin-top: 9px;
    font-size: 10.5px;
    line-height: 14.6px;
  }
  .contacts li {
    display: flex;
    align-items: center;
    gap: 7px;
  }
  .contacts svg { width: 10px; height: 10px; flex: none; }

  .decor-block {
    position: absolute;
    left: 386px;
    top: 148px;
    right: 0;
    bottom: 0;
    background: var(--faint);
    opacity: 0.8;
  }

  .brand {
    position: absolute;
    left: 0;
    width: 540px;
    top: 134px;
    text-align: center;
  }
  .brand__mark {
    display: flex;
    align-items: center;
    justify-content: center;
    gap: 8px;
  }
  .brand__square {
    width: 10px;
    height: 10px;
    background: var(--teal);
  }
  .brand__name {
    font-family: "Arimo", sans-serif;
    font-size: 17px;
    font-weight: 400;
    color: var(--teal);
  }
  .brand__tagline {
    margin: 12px 0 0;
    font-family: "Arimo", sans-serif;
    font-size: 11.5px;
    letter-spacing: 0.6px;
    color: var(--ink);
  }
</style>
</head>
<body>
<main class="canvas">
  <section class="card card--front">
    <div class="decor-block"></div>
    <div class="holder">
      <h1 class="holder__name">DANIEL REYES</h1>
      <p class="holder__title">CEO/FOUNDER</p>
      <address class="address">
        Shelter Bridge Alliance<br>
        412 Willow Court<br>
        Juneau, Alaska 99801
      </address>
      <ul class="contacts">
        <li>
          <svg viewBox="0 0 10 10"><path fill="var(--teal)" d="M2 0.5l2 2-1 1.2c.6 1.3 1.6 2.3 2.9 2.9l1.2-1 2 2-1.3 1.8C4.7 9.3.7 5.3.3 2z"/></svg>
          555 214 7789
        </li>
        <li>
          <svg viewBox="0 0 10 10"><rect x="0.5" y="2" width="9" height="6.5" fill="var(--teal)"/><path d="M0.8 2.3L5 5.6l4.2-3.3" stroke="#fff" stroke-width="0.9" fill="none"/></svg>
          daniel@shelterbridge.org
        </li>
        <li>
          <svg viewBox="0 0 10 10"><circle cx="5" cy="5" r="4.6" fill="var(--teal)"/><path d="M3 2.5c1 .5 1 1.5 0 2s.5 1.5 1.5 1.5M6.5 6.5c.8-.3 1.6.2 1.7 1" stroke="#fff" stroke-width="0.8" fill="none"/></svg>
          www.shelterbridge.org
        </li>
      </ul>
    </div>
  </section>

  <section class="card card--back">
    <div class="brand">
      <div class="brand__mark">
        <span class="brand__square"></span>
        <span class="brand__name">Shelter Bridge Alliance</span>
      </div>
      <p class="brand__tagline">Opening doors for every family</p>
    </div>
  </section>
</main>
</body>
</html>
```